I have a logo and need to design the business card and stationery.
Updates

The uploaded logo image named as GREYMARSH CONSTRUCTION which is to be replaced to GREYMARSH CONTRACTS. Kindly add below details and submit the designs- Company name- Greymarsh Engineering Contracts LLP Name & Post- Kelvan Joshi (Designated Partner) Address- Block No.317, Wing C, Tulvo Trade Court, Manek Pural Road, Ruparel Industrial Estate, Goregaon(E), Mumbai - 400 063 Contact- +91 97415 60382 Email- kelvanjoshi@mailbrook.example Website- www.greymarshcontracts.example Contact for Letterhead- +91-22-28754193

Hi Tovin Rahul, We are liking your Design #28860835. We have suggested some changes which are mentioned in feedback. Kindly revert with it asap to finalize this design.

Colors

Designer to choose colors to be used in the design.

```html
<!DOCTYPE html>
<html lang="en">
<head>
<meta charset="utf-8">
<title>Greymarsh Contracts – Stationery</title>
<link rel="stylesheet" href="https://fonts.googleapis.com/css2?family=Questrial&display=swap">
<style>
:root{
  --backdrop:#3a3b3d;
  --paper:#ffffff;
  --charcoal:#333333;
  --slate:#666666;
  --ink:#3b3b3b;
  --muted:#5a5a5a;
}
*{margin:0;padding:0;box-sizing:border-box}
html,body{width:1200px;height:800px;overflow:hidden}
body{background:var(--backdrop);font-family:"Questrial",sans-serif;color:var(--ink);position:relative}
.sheet{position:absolute;background:var(--paper);box-shadow:0 3px 8px rgba(0,0,0,.45)}
.sheet.dark{background:var(--charcoal)}
.brand{position:absolute;display:flex;flex-direction:column;align-items:center;text-transform:uppercase;color:var(--charcoal);line-height:1}
.brand .mark{background:var(--charcoal);margin-bottom:5px}
.brand .name{letter-spacing:.06em}
.brand .sub{letter-spacing:.42em;margin-top:2px}
.brand.light{color:#fff}
.brand.light .mark{background:#fff}
.block-square{position:absolute;background:var(--charcoal)}
.address{position:absolute;font-size:6.2px;line-height:9.2px;color:var(--muted)}
.icon{display:inline-block;width:6px;height:6px;vertical-align:-1px;margin-right:3px}

/* business card front */
.card-front{left:99px;top:56px;width:206px;height:124px}
.card-front .person{position:absolute;left:64px;top:31px}
.card-front .person-name{font-size:8.5px;color:#222}
.card-front .person-role{font-size:4.5px;color:var(--muted)}
.card-front .details{position:absolute;left:64px;top:53px;font-size:4.6px;line-height:6.2px;color:var(--muted)}
.card-front .details p{margin-bottom:8px}
.card-front .details p.tight{margin-bottom:1px}

/* business card back */
.card-back{left:371px;top:56px;width:205px;height:124px}
.card-back .web{position:absolute;left:0;right:0;top:100px;text-align:center;font-size:5px;letter-spacing:.2em;color:#ddd}

/* envelope */
.envelope{left:99px;top:231px;width:477px;height:240px}
.envelope .flap{position:absolute;left:0;top:0;width:100%;height:56px;background:var(--charcoal);border-radius:0 0 26px 26px}

/* compliment slip */
.slip{left:99px;top:504px;width:477px;height:240px;overflow:hidden}

/* letterhead */
.letterhead{left:611px;top:56px;width:490px;height:688px;overflow:hidden}
.letterhead .salutation{position:absolute;left:39px;top:174px;font-size:12.5px;color:#333}
.letterhead .body{position:absolute;left:39px;top:200px;width:413px;font-size:8.2px;line-height:9.6px;text-align:justify;color:var(--muted)}
.letterhead .body p{margin-bottom:9.6px}
.letterhead .body p.join{margin-bottom:0}
.letterhead .signature{position:absolute;left:356px;top:454px;width:94px;height:60px;background:linear-gradient(90deg,#f3f3f3,#e6e6e6)}
.letterhead .signatory{position:absolute;left:337px;top:524px;font-size:10px;color:var(--muted)}
.letterhead .contact{position:absolute;left:322px;top:624px;border-left:1px solid #333;padding-left:6px;font-size:8px;line-height:12px;color:#444}
</style>
</head>
<body>

<!-- Business card front -->
<section class="sheet card-front">
  <div class="block-square" style="left:0;top:29px;width:58px;height:66px"></div>
  <div class="person">
    <div class="person-name"><strong>Kelvan</strong> Joshi</div>
    <div class="person-role">(Designated Partner)</div>
  </div>
  <div class="details">
    <p><svg class="icon" viewBox="0 0 10 10"><circle cx="5" cy="5" r="5" fill="#333"/><circle cx="5" cy="4.3" r="1.6" fill="#fff"/></svg>Block No.317, Wing C, Tulvo Trade Court,<br>&nbsp;&nbsp;&nbsp;&nbsp;Manek Pural Road, Ruparel Industrial Estate,<br>&nbsp;&nbsp;&nbsp;&nbsp;Goregaon(E), Mumbai - 400 063</p>
    <p class="tight"><svg class="icon" viewBox="0 0 10 10"><circle cx="5" cy="5" r="5" fill="#333"/><path d="M3 3l1 0 .6 1.4-.6.5a4 4 0 0 0 1.6 1.6l.5-.6L7.5 6.5v1A4.5 4.5 0 0 1 3 3z" fill="#fff"/></svg>+91 97415 60382</p>
    <p><svg class="icon" viewBox="0 0 10 10"><circle cx="5" cy="5" r="5" fill="#333"/><rect x="2.6" y="3.3" width="4.8" height="3.4" fill="#fff"/></svg>kelvanjoshi@mailbrook.example</p>
  </div>
  <div class="brand" style="left:146px;top:107px">
    <span class="name" style="font-size:5.2px">Greymarsh</span>
    <span class="sub" style="font-size:3px">Contracts</span>
  </div>
</section>

<!-- Business card back -->
<section class="sheet dark card-back">
  <div class="brand light" style="left:0;right:0;top:40px">
    <span class="mark" style="width:22px;height:22px"></span>
    <span class="name" style="font-size:9px">Greymarsh</span>
    <span class="sub" style="font-size:5px">Contracts</span>
  </div>
  <div class="web">www.greymarshcontracts.example</div>
</section>

<!-- Envelope -->
<section class="sheet envelope">
  <div class="flap">
    <div class="brand light" style="left:0;right:0;top:18px">
      <span class="name" style="font-size:12.5px">Greymarsh</span>
      <span class="sub" style="font-size:6.5px">Contracts</span>
    </div>
  </div>
</section>

<!-- Compliment slip -->
<section class="sheet slip">
  <div class="brand" style="left:14px;top:16px;width:116px">
    <span class="mark" style="width:34px;height:34px"></span>
    <span class="name" style="font-size:12.5px">Greymarsh</span>
    <span class="sub" style="font-size:6.5px">Contracts</span>
  </div>
  <div class="address" style="left:15px;top:194px">
    <svg class="icon" viewBox="0 0 10 10"><path d="M5 0a3.5 3.5 0 0 1 3.5 3.5C8.5 6 5 10 5 10S1.5 6 1.5 3.5A3.5 3.5 0 0 1 5 0z" fill="#333"/><circle cx="5" cy="3.5" r="1.3" fill="#fff"/></svg>Block No.317, Wing C, Tulvo Trade Court,<br>&nbsp;&nbsp;&nbsp;&nbsp;&nbsp;Manek Pural Road, Ruparel Industrial Estate,<br>&nbsp;&nbsp;&nbsp;&nbsp;&nbsp;Goregaon(E), Mumbai - 400 063
  </div>
  <div class="block-square" style="left:386px;top:123px;width:91px;height:104px"></div>
</section>

<!-- Letterhead -->
<section class="sheet letterhead">
  <div class="brand" style="left:39px;top:49px;width:116px">
    <span class="mark" style="width:35px;height:35px"></span>
    <span class="name" style="font-size:12.5px">Greymarsh</span>
    <span class="sub" style="font-size:6.5px">Contracts</span>
  </div>
  <div class="address" style="left:316px;top:80px;font-size:6.8px;line-height:9.8px">
    <svg class="icon" viewBox="0 0 10 10"><path d="M5 0a3.5 3.5 0 0 1 3.5 3.5C8.5 6 5 10 5 10S1.5 6 1.5 3.5A3.5 3.5 0 0 1 5 0z" fill="#333"/><circle cx="5" cy="3.5" r="1.3" fill="#fff"/></svg>Block No.317, Wing C, Tulvo Trade Court,<br>&nbsp;&nbsp;&nbsp;&nbsp;&nbsp;Manek Pural Road, Ruparel Industrial Estate,<br>&nbsp;&nbsp;&nbsp;&nbsp;&nbsp;Goregaon(E), Mumbai - 400 063
  </div>

  <div class="salutation">Dear Mr.Kelvan</div>
  <div class="body">
    <p>Lorem ipsum dolor sit amet, consectetuer adipiscing elit, sed diam nonummy nibh euismod tincidunt ut laoreet dolore magna aliquam erat volutpat. Ut wisi enim ad minim veniam, quis nostrud exerci tation ullamcorper suscipit lobortis nisl ut aliquip ex ea commodo consequat. Duis autem vel eum iriure dolor in hendrerit in vulputate velit esse molestie consequat, vel illum dolore eu feugiat nulla facilisis at vero eros et accumsan et iusto odio dignissim qui blandit praesent luptatum zzril delenit augue duis dolore te feugait nulla facilisi.</p>
    <p class="join">Lorem ipsum dolor sit amet, cons ectetuer adipiscing elit, sed diam nonummy nibh euismod tincidunt ut laoreet dolore magna aliquam erat volutpat. Ut wisi enim ad minim veniam, quis nostrud exerci tation ullamcorper suscipit lobortis nisl ut aliquip ex ea commodo consequat.</p>
    <p style="margin-bottom:19px">Lorem ipsum dolor sit amet, consectetuer adipiscing elit, sed diam nonummy nibh euismod tincidunt ut laoreet dolore magna aliquam erat</p>
    <p>Lorem ipsum dolor sit amet, cons ectetuer adipiscing elit, sed diam nonummy nibh euismod tincidunt ut laoreet dolore magna aliquam erat volutpat. Ut wisi enim ad minim veniam, quis nostrud exerci tation ullamcorper suscipit lobortis nisl ut aliquip ex ea commodo consequat. Lorem ipsum dolor sit zamet, consectetuer adipiscing elit, sed diam nonummy nibh euismod tincidunt ut laoreet dolore magna aliquam erat volutpat. Ut wisi enim ad minim veniam, quis nostrud exerci tation ullamcorper suscipit lobortis nisl ut aliquip ex ea commodo consequat. Duis autem vel eum iriure dolor in hendrerit in vulputate velit esse molestie consequat, vel illum dolore eu feugiat nulla facilisis at vero eros et accumsan et iusto odio dignissim qui blandit praesent luptatum zzril delenit augue duis dolore te feugait nulla facilisi. Lorem ipsum dolor sit amet, cons ectetuer adipiscing elit, sed diam nonummy nibh euismod tincidunt ut laoreet dolore magna aliquam erat volutpat. Ut wisi enim ad minim veniam, quis nostrud exerci tation ullamcorper suscipit lobortis nisl ut aliquip ex ea commodo consequat.</p>
  </div>

  <div class="signature" role="img" aria-label="Handwritten signature of the Managing Director"></div>
  <div class="signatory">Managing Director</div>

  <div class="block-square" style="left:0;top:561px;width:97px;height:112px"></div>

  <div class="contact">
    <div><svg class="icon" viewBox="0 0 10 10"><circle cx="5" cy="5" r="5" fill="#333"/><path d="M3 3l1 0 .6 1.4-.6.5a4 4 0 0 0 1.6 1.6l.5-.6L7.5 6.5v1A4.5 4.5 0 0 1 3 3z" fill="#fff"/></svg>+91-22-28754193</div>
    <div><svg class="icon" viewBox="0 0 10 10"><circle cx="5" cy="5" r="5" fill="#333"/><rect x="2.6" y="3.3" width="4.8" height="3.4" fill="#fff"/></svg>kelvanjoshi@mailbrook.example</div>
    <div><svg class="icon" viewBox="0 0 10 10"><circle cx="5" cy="5" r="4.4" fill="none" stroke="#333" stroke-width="1.2"/><path d="M.6 5h8.8M5 .6c-2.4 2.6-2.4 6.2 0 8.8M5 .6c2.4 2.6 2.4 6.2 0 8.8" fill="none" stroke="#333" stroke-width=".8"/></svg>www.greymarshcontracts.example</div>
  </div>
</section>

</body>
</html>
```